Social Media Graphics - Oakline Push REVISED

Create 6-7 individual social media graphics (square size) to encourage folks to join our online course called:

The Harvest Ledger Circle
How to Launch a Multi-Million Business From Scratch
Sign Up Today!

IMPORTANT: Make the largest and most prominent text on the graphic be: How to Launch a Multi-Million Business From Scratch

For the color scheme of the graphics, let's try a blue color palette; make sure the graphics appeal to both men and women

Make sure each graphic contains 1 of the 3 pics attached (crop pic as needed); and make sure one of the graphics is all TEXT only.

Target Market(s)

men and women looking to start a business

Industry/Entity Type

Entrepreneurship

Colors
0054AA
0677BA
7BADD7
CADEEF
E8F1F8

Requirements
Must have
• All the text and use the 3 pics provided; one graphic can be all text; Simple, modern design that's easy to read

```html
<!DOCTYPE html>
<html lang="en">
<head>
<meta charset="utf-8">
<title>The Harvest Ledger Circle – Social Graphics</title>
<link href="https://fonts.googleapis.com/css2?family=Montserrat:wght@500;700;800;900&family=Bodoni+Moda:opsz,wght@6..96,800;6..96,900&display=swap" rel="stylesheet">
<style>
  :root{
    --sheet:#5b5b5b;
    --blue-deep:#0054AA;
    --blue-mid:#0677BA;
    --blue-soft:#7BADD7;
    --blue-pale:#CADEEF;
    --blue-mist:#E8F1F8;
    --navy:#0b2447;
    --white:#ffffff;
    --blush:#f6c9d4;
    --photo-a:#4a6f95;
    --photo-b:#c9a58a;
  }
  *{box-sizing:border-box;margin:0;padding:0}
  html,body{width:802px;height:1200px;overflow:hidden;background:var(--sheet)}
  .sheet{position:relative;width:802px;height:1200px;background:var(--sheet)}
  .tile{position:absolute;width:361px;height:362px;overflow:hidden;font-family:'Montserrat',sans-serif}
  .tile--a{left:32px;top:32px;background:var(--blue-deep)}
  .tile--b{left:409px;top:32px;background:var(--white)}
  .tile--c{left:32px;top:411px;background:var(--white)}
  .tile--d{left:409px;top:411px;background:var(--white)}
  .tile--e{left:32px;top:792px}
  .tile--f{left:409px;top:792px;background:var(--blue-deep)}
  .abs{position:absolute}
  .photo{position:absolute;background:linear-gradient(160deg,var(--photo-a),var(--photo-b))}
  .serif{font-family:'Bodoni Moda',serif;font-weight:900}

  /* tile A */
  .a-head{left:18px;top:16px;color:var(--white);font-weight:900;font-size:29px;line-height:1.02}
  .a-box{left:184px;top:14px;width:162px;height:64px;border:2px solid var(--white);color:var(--white);padding:6px 8px;font-weight:800;font-size:15px;line-height:1.05}
  .a-box small{display:block;font-size:9px;font-weight:700;margin-top:3px}
  .a-bar{left:16px;top:88px;width:330px;height:30px;background:var(--white);color:var(--blue-deep);font-weight:900;font-size:16px;text-align:center;line-height:30px}
  .a-cta{left:0;top:126px;width:100%;text-align:center;color:var(--white);font-weight:800;font-size:9px;letter-spacing:.5px}
  .a-photo{left:40px;top:146px;width:281px;height:216px;border-radius:120px 120px 0 0}

  /* tile B */
  .b-corner{width:150px;height:150px;border-radius:50%;background:var(--blue-mist)}
  .b-cta{left:0;top:8px;width:100%;text-align:center;color:var(--blue-mid);font-weight:800;font-size:8px}
  .b-head{left:0;top:20px;width:100%;text-align:center;color:var(--navy);font-weight:900;font-size:30px}
  .b-sub{left:0;top:56px;width:100%;text-align:center;color:var(--navy);font-weight:700;font-size:11px}
  .b-ring{left:112px;top:90px;width:178px;height:178px;border-radius:50%;background:var(--blue-pale)}
  .b-photo{left:96px;top:80px;width:170px;height:170px;border-radius:50%}
  .b-band{left:0;top:296px;width:100%;height:46px;background:var(--blue-deep);color:var(--white);font-weight:900;font-size:18px;text-align:center;line-height:46px}

  /* tile C */
  .c-cta{left:0;top:10px;width:100%;text-align:center;color:var(--blue-mid);font-weight:800;font-size:8px}
  .c-head{left:0;top:22px;width:100%;text-align:center;color:var(--navy);font-weight:900;font-size:31px}
  .c-sub{left:0;top:60px;width:100%;text-align:center;color:var(--navy);font-weight:700;font-size:12px}
  .c-name{left:0;top:80px;width:100%;text-align:center;color:var(--blue-mid);font-weight:700;font-size:13px}
  .c-art{left:0;top:100px}

  /* tile D */
  .d-blush{left:170px;top:0;width:191px;height:362px;background:var(--blush);border-radius:0 0 0 90px}
  .d-photo{left:178px;top:100px;width:183px;height:262px;border-radius:90px 90px 0 0}
  .d-text{left:16px;top:22px;color:var(--navy);line-height:1}
  .d-l1{font-size:30px}
  .d-l2{font-size:30px;white-space:nowrap}
  .d-l2 span{font-size:13px;vertical-align:middle}
  .d-l3{font-size:34px;color:var(--blue-deep)}
  .d-l4{font-size:12px;font-family:'Montserrat',sans-serif;font-weight:800;margin-top:4px}
  .d-btn{left:16px;top:190px;width:96px;height:22px;border-radius:11px;background:var(--blue-deep);color:var(--white);font-weight:800;font-size:8px;text-align:center;line-height:22px}
  .d-name{left:16px;top:226px;color:var(--navy);line-height:1.02}
  .d-name .t{font-size:16px}
  .d-name .b{font-size:26px;color:var(--blue-deep)}

  /* tile E */
  .e-photo{left:0;top:0;width:361px;height:362px}
  .e-panel{left:0;top:0}
  .e-name{left:18px;top:18px;color:var(--white);font-weight:900;font-size:15px;line-height:1.1}
  .e-head{left:18px;top:128px;color:var(--white);font-weight:900;font-size:30px;line-height:1.02}
  .e-sub{left:18px;top:232px;color:var(--white);font-weight:700;font-size:11px;line-height:1.2}
  .e-cta{left:18px;top:290px;color:var(--white);font-weight:800;font-size:8px;border-bottom:1px solid var(--white);padding-bottom:2px}

  /* tile F */
  .f-text{left:20px;top:24px;color:var(--white);line-height:.98}
  .f-l1{font-size:36px}
  .f-l2{font-size:36px;white-space:nowrap}
  .f-l2 span{font-size:15px;vertical-align:middle}
  .f-l3{font-size:52px}
  .f-l4{font-family:'Montserrat',sans-serif;font-weight:800;font-size:12px;margin-top:6px}
  .f-name{left:0;top:262px;width:100%;text-align:center;color:var(--white);font-weight:900;font-size:16px}
  .f-btn{left:110px;top:292px;width:141px;height:28px;border-radius:14px;background:var(--white);color:var(--blue-deep);font-weight:900;font-size:10px;text-align:center;line-height:28px}
</style>
</head>
<body>
<main class="sheet">

  <section class="tile tile--a">
    <div class="abs a-head">HOW TO<br>LAUNCH A</div>
    <div class="abs a-box">MULTI-MILLION<br>BUSINESS<small>FROM SCRATCH</small></div>
    <div class="abs a-bar">THE HARVEST LEDGER CIRCLE</div>
    <div class="abs a-cta">SIGN UP TODAY!</div>
    <div class="photo a-photo" role="img" aria-label="Photo of a smiling woman and man, course hosts"></div>
  </section>

  <section class="tile tile--b">
    <div class="abs b-corner" style="left:-70px;top:150px"></div>
    <div class="abs b-corner" style="left:280px;top:-60px"></div>
    <div class="abs b-cta">SIGN UP TODAY!</div>
    <div class="abs b-head">HOW TO LAUNCH A</div>
    <div class="abs b-sub">MULTI-MILLION BUSINESS FROM SCRATCH</div>
    <div class="abs b-ring"></div>
    <div class="photo b-photo" role="img" aria-label="Photo of a woman and man standing together, course hosts"></div>
    <div class="abs b-band">THE HARVEST LEDGER CIRCLE</div>
  </section>

  <section class="tile tile--c">
    <div class="abs c-cta">SIGN UP TODAY!</div>
    <div class="abs c-head">HOW TO LAUNCH A</div>
    <div class="abs c-sub">MULTI-MILLION BUSINESS FROM SCRATCH</div>
    <div class="abs c-name">The Harvest Ledger Circle</div>
    <svg class="abs c-art" width="361" height="262" viewBox="0 0 361 262" role="img" aria-label="Photo of a man and woman smiling, course hosts">
      <defs>
        <linearGradient id="cPhoto" x1="0" y1="0" x2="1" y2="1">
          <stop offset="0" stop-color="#4a6f95"/>
          <stop offset="1" stop-color="#c9a58a"/>
        </linearGradient>
      </defs>
      <path d="M0 40 Q180 -10 361 40 L361 262 L0 262 Z" fill="url(#cPhoto)"/>
      <path d="M0 30 Q180 -20 361 30" fill="none" stroke="#0054AA" stroke-width="6"/>
    </svg>
  </section>

  <section class="tile tile--d">
    <div class="abs d-blush"></div>
    <div class="photo d-photo" role="img" aria-label="Photo of a woman and man, course hosts"></div>
    <div class="abs d-text serif">
      <div class="d-l1">HOW TO</div>
      <div class="d-l2">LAUNCH A <span>MULTI-MILLION</span></div>
      <div class="d-l3">BUSINESS</div>
      <div class="d-l4">FROM SCRATCH</div>
    </div>
    <div class="abs d-btn">SIGN UP TODAY!</div>
    <div class="abs d-name serif">
      <div class="t">THE</div>
      <div class="b">HARVEST<br>LEDGER</div>
      <div class="t">CIRCLE</div>
    </div>
  </section>

  <section class="tile tile--e">
    <div class="photo e-photo" role="img" aria-label="Photo of a man in a blazer presenting, course host"></div>
    <svg class="abs e-panel" width="361" height="362" viewBox="0 0 361 362" aria-hidden="true">
      <path d="M0 0 H150 Q215 181 150 362 H0 Z" fill="#0677BA"/>
    </svg>
    <div class="abs e-name">THE HARVEST<br>LEDGER CIRCLE</div>
    <div class="abs e-head">HOW TO<br>LAUNCH A</div>
    <div class="abs e-sub">MULTI-MILLION<br>BUSINESS<br>FROM SCRATCH</div>
    <div class="abs e-cta">SIGN UP TODAY!</div>
  </section>

  <section class="tile tile--f">
    <div class="abs f-text serif">
      <div class="f-l1">HOW TO</div>
      <div class="f-l2">LAUNCH A <span>MULTI-MILLION</span></div>
      <div class="f-l3">BUSINESS</div>
      <div class="f-l4">FROM SCRATCH</div>
    </div>
    <div class="abs f-name">THE HARVEST LEDGER CIRCLE</div>
    <div class="abs f-btn">SIGN UP TODAY!</div>
  </section>

</main>
</body>
</html>
```